Payment company requires web design

We need a web design for a new company based in Singapore.

The company focuses on providing 2 key products: 1) an alternative payment option (i.e. like quib or trelloquin options) on the traditional checkout process 2) a replacement/outsource of a merchants payment page. Key in the UX flow is a end customer dashboard that manages all payments.

We look to provide a simple, fluid and easy to use payment process. The dashboard is minimalistic that allows easy navigation, review of transactions and all available options through gamification.

The final design should communicate ease of use, flexibility and transparency.

Target Market(s)

The value is for the merchant - retail/travel/insurance companies. However its the merchant's end customers that are the target and who the UX is built for.

Industry/Entity Type

It Company

Logo Text

zelnar

Number of Pages Required

5+ page

Colors
ec1f27

Requirements
Must have
• 7 pages mimicking UX flow
• payment page * 2 - 1) alternative payment type 2) outsource of merchants payment page to our business
• our landing page
• end customer verification page
• end customer registration
• customer dashboard
• UX flow in attached file
Nice to have
• open to ideas
• have asked for the logo to be added
• logo to have the colour red (chinese for prosperity)
• the company is all about flexibility, transparency in personal finance management with the option of instalment payments

```html
<!DOCTYPE html>
<html lang="en">
<head>
<meta charset="utf-8">
<title>Zelnar – Personal Finance Management</title>
<link href="https://fonts.googleapis.com/css2?family=Open+Sans:wght@400;600;700;800&display=swap" rel="stylesheet">
<style>
:root{
  --red:#ec1f27;
  --ink:#222222;
  --text:#555555;
  --muted:#777777;
  --band:#efefef;
  --line:#e4e4e4;
  --white:#ffffff;
}
*{margin:0;padding:0;box-sizing:border-box}
html,body{width:1200px;height:2667px;overflow:hidden;background:var(--white)}
body{font-family:"Open Sans",Arial,sans-serif;color:var(--text);position:relative}
.btn{position:absolute;background:var(--red);color:var(--white);font-weight:700;text-transform:uppercase;display:flex;align-items:center;justify-content:center;letter-spacing:.3px;border-radius:2px;white-space:nowrap}

/* header */
.site-header{position:absolute;left:0;top:0;width:1200px;height:90px;border-top:3px solid var(--red);background:var(--white);box-shadow:0 1px 3px rgba(0,0,0,.08);z-index:2}
.brand{position:absolute;left:160px;top:27px;font-size:31px;font-weight:800;color:var(--red);letter-spacing:.5px;line-height:1}
.nav a{position:absolute;top:39px;font-size:11px;font-weight:600;color:var(--ink);text-decoration:none;line-height:1;white-space:nowrap}
.nav a.active{color:var(--red)}
.nav .caret{position:absolute;left:482px;top:80px;width:0;height:0;border-left:8px solid transparent;border-right:8px solid transparent;border-bottom:8px solid var(--red)}
.login{left:969px;top:31px;width:69px;height:31px;font-size:11px}

/* hero */
.hero{position:absolute;left:0;top:90px;width:1200px;height:503px;background:linear-gradient(90deg,#f3f3f3 0%,#f1f1f1 40%,#ececec 100%)}
.hero-photo{position:absolute;left:489px;top:0;width:711px;height:503px;background:linear-gradient(120deg,#f4f4f4 0%,#e8e4df 35%,#d9cfc6 60%,#c9c3be 100%)}
.hero-copy{position:absolute;left:160px;top:140px;width:420px}
.hero-copy h1{font-weight:400;font-size:27px;line-height:38px;color:var(--ink)}
.hero-copy h1 .accent{color:var(--red)}
.hero-copy p{margin-top:14px;font-size:14.5px;line-height:24px;color:#333}
.register{left:160px;top:342px;width:127px;height:36px;font-size:13px}
.slide-arrow{position:absolute;top:234px;width:34px;height:34px;border:1.5px solid #c9c9c9;border-radius:50%}
.slide-arrow svg{display:block}

/* section titles */
.section-title{position:absolute;left:0;width:1200px;text-align:center;font-size:23px;font-weight:600;text-transform:uppercase}
.section-title.red{color:var(--red)}
.section-title.dark{color:var(--ink)}

/* welcome */
.welcome-lead{position:absolute;left:0;top:683px;width:1200px;text-align:center;font-size:17px;font-weight:600;color:var(--ink)}
.welcome-body{position:absolute;left:160px;top:720px;width:880px;text-align:center;font-size:10.5px;line-height:19px;color:var(--text)}
.read-more{font-size:10px}
.divider{position:absolute;left:160px;top:893px;width:880px;height:1px;background:var(--line)}

/* who */
.who-item{position:absolute;width:420px;height:100px}
.who-photo{position:absolute;width:92px;height:92px;border-radius:50%;border:3px solid #ddd}
.who-item h3{position:absolute;font-size:14px;font-weight:600;color:var(--ink);text-transform:uppercase;white-space:nowrap;line-height:18px}
.who-item p{position:absolute;font-size:10.5px;line-height:19px;color:var(--text);width:300px}

/* how */
.how{position:absolute;left:0;top:1300px;width:1200px;height:428px;background:var(--band)}
.step{position:absolute;top:136px;width:200px;text-align:center}
.step-icon{margin:0 auto;width:98px;height:98px;border:3px solid var(--red);border-radius:50%;background:var(--white);display:flex;align-items:center;justify-content:center}
.step h3{margin-top:30px;font-size:13px;font-weight:600;color:var(--ink);text-transform:uppercase}
.step p{margin:14px auto 0;width:190px;font-size:10.5px;line-height:18px;color:var(--text)}
.flow-arrow{position:absolute;top:195px}

/* reasons */
.reason{position:absolute;top:1835px;width:276px}
.reason-photo{width:276px;height:149px;border:4px solid var(--white);box-shadow:0 0 0 1px #ddd}
.reason h3{margin-top:14px;font-size:15px;font-weight:700;color:var(--ink)}
.reason p{margin-top:10px;font-size:10.5px;line-height:19px;color:var(--text)}
.reason .btn{position:relative;margin-top:20px;width:98px;height:31px}

/* cta */
.cta{position:absolute;left:0;top:2201px;width:1200px;height:203px;background:var(--band);text-align:center}
.cta h2{position:absolute;left:0;top:58px;width:1200px;font-size:22px;line-height:32px;font-weight:600;color:var(--ink)}
.cta .btn{left:533px;top:139px;width:134px;height:33px;font-size:10px}

/* footer */
.footer-col{position:absolute;top:2466px}
.footer-col h4{font-size:12px;font-weight:700;color:var(--ink);text-transform:uppercase;margin-bottom:20px}
.footer-col li{list-style:none;font-size:11px;line-height:21px;color:#444;white-space:nowrap}
.socials{display:flex;gap:6px;margin-top:-4px}
.socials span{width:27px;height:27px;border-radius:50%;display:block}
.copyright{margin-top:22px;font-size:10.5px;color:#333;line-height:19px;white-space:nowrap}
.copyright a{color:#333;text-decoration:none;margin-right:10px}
</style>
</head>
<body>

<header class="site-header">
  <div class="brand">ZELNAR</div>
  <nav class="nav">
    <a class="active" style="left:473px">HOME</a>
    <a style="left:544px">ABOUT</a>
    <a style="left:619px">FOR MERCHANT PAYMENT</a>
    <a style="left:800px">FOR PERSONAL PAYMENT</a>
    <span class="caret"></span>
  </nav>
  <a class="btn login">Log in</a>
</header>

<section class="hero">
  <div class="hero-photo" role="img" aria-label="Happy young couple at a laptop, one holding a payment card"></div>
  <div class="hero-copy">
    <h1><span class="accent">We are about</span><br>Flexibility Transparency in<br><span class="accent">Personal Finance Management</span></h1>
    <p>Lorem ipsum dolor sit amet, consectetur adipiscing elit, sed do eiusmod tempor incididunt ut laboreloreit ansetetmmo.</p>
  </div>
  <a class="btn register">Register</a>
  <span class="slide-arrow" style="left:27px"><svg width="31" height="31" viewBox="0 0 31 31"><path d="M17.5 11l-5 4.5 5 4.5" fill="none" stroke="#bbb" stroke-width="1.5"/></svg></span>
  <span class="slide-arrow" style="left:1139px"><svg width="31" height="31" viewBox="0 0 31 31"><path d="M13.5 11l5 4.5-5 4.5" fill="none" stroke="#bbb" stroke-width="1.5"/></svg></span>
</section>

<h2 class="section-title red" style="top:636px">Welcome to Zelnar</h2>
<p class="welcome-lead">Lorem ipsum dolor sit amet, consectetur adipiscing elit, sed deiusm tempor incididunt ut laborelo</p>
<p class="welcome-body">Sed ut perspiciatis unde omnis iste natus error sit voluptatem accusantium dolore mq ue laudantium, totam rem aperiam, eaque ipsa quae ab illo inventore veritatis et quasi architecto beatae vitae dicta sunt explicabo. Nemo enim ipsam volupta tem quia volup tas sit aspernatur aut odit aut fugit, sed quia conse quun tur mag ni dolores eos qui ratione voluptatem sequi nesciuSed ut perspiciatis unde omnis iste natus error sit voluptatem accusantium dolore mq ue laudantium, totam rem aperiam, eaque ipsa quae ab illo inventore veritatis et quasi architecto beatae vitae dicta sunt explicabo. Nemo enim ipsam volupta tem quia volup tas sit aspernatur aut odit aut fugit.</p>
<a class="btn read-more" style="left:551px;top:823px;width:96px;height:32px">Read more &rsaquo;</a>
<div class="divider"></div>

<h2 class="section-title red" style="top:930px">Who is Zelnar</h2>

<div class="who-item" style="left:162px;top:1008px">
  <div class="who-photo" style="left:0;top:0;background:linear-gradient(135deg,#c9b8a6,#6d5a4d)" role="img" aria-label="Shopper holding shopping bags"></div>
  <h3 style="left:108px;top:10px">Consumers</h3>
  <p style="left:108px;top:32px">Sed ut perspiciatis unde omnis iste natus error sit volpatem accusantium dolore mq ue laudantium, totam rem aperiam, eaque ipsa quae ab illo inventore verit.</p>
</div>
<div class="who-item" style="left:635px;top:1012px">
  <div class="who-photo" style="left:0;top:0;background:linear-gradient(135deg,#b9a796,#4e4440)" role="img" aria-label="Card being inserted into a payment terminal"></div>
  <h3 style="left:108px;top:10px">Merchants</h3>
  <p style="left:108px;top:32px">Sed ut perspiciatis unde omnis iste natus error sit vup tatem accusantium dolore mq ue laudantium, totam rem aperiam, eaque ipsa quae ab illo inventore verit.</p>
</div>
<div class="who-item" style="left:167px;top:1133px">
  <div class="who-photo" style="left:0;top:0;background:linear-gradient(135deg,#e2d6cc,#a58f80)" role="img" aria-label="Hands exchanging a payment card"></div>
  <h3 style="left:105px;top:7px">Instalment Payments</h3>
  <p style="left:105px;top:31px">Sed ut perspiciatis unde omnis iste natus errort volup tatem accusantium dolore mq ue laudantium, totam rem aperiam, eaque ipsa quae ab illo inventore verit.</p>
</div>
<div class="who-item" style="left:637px;top:1140px">
  <div class="who-photo" style="left:0;top:0;background:linear-gradient(135deg,#d8d8d8,#8b8e94)" role="img" aria-label="Person paying with a mobile phone"></div>
  <h3 style="left:106px;top:7px">Personal Financial Management</h3>
  <p style="left:106px;top:31px">Sed ut perspiciatis unde omnis iste natus error sit volup tem accusantium dolore mq ue laudantium, totam rem aperiam, eaque ipsa quae ab illo inventore verit.</p>
</div>

<section class="how">
  <h2 class="section-title dark" style="top:58px">How does it work?</h2>

  <svg class="flow-arrow" style="left:320px" width="100" height="40" viewBox="0 0 100 40"><path d="M4 28 Q45 0 86 22" fill="none" stroke="#d6d6d6" stroke-width="7"/><path d="M80 10 L96 28 L74 30 Z" fill="#d6d6d6"/></svg>
  <svg class="flow-arrow" style="left:555px" width="100" height="40" viewBox="0 0 100 40"><path d="M4 28 Q45 0 86 22" fill="none" stroke="#d6d6d6" stroke-width="7"/><path d="M80 10 L96 28 L74 30 Z" fill="#d6d6d6"/></svg>
  <svg class="flow-arrow" style="left:790px" width="100" height="40" viewBox="0 0 100 40"><path d="M4 28 Q45 0 86 22" fill="none" stroke="#d6d6d6" stroke-width="7"/><path d="M80 10 L96 28 L74 30 Z" fill="#d6d6d6"/></svg>

  <div class="step" style="left:149px">
    <div class="step-icon"><svg width="46" height="40" viewBox="0 0 46 40"><ellipse cx="22" cy="21" rx="17" ry="13" fill="var(--red)"/><rect x="10" y="30" width="6" height="8" fill="var(--red)"/><rect x="27" y="30" width="6" height="8" fill="var(--red)"/><path d="M37 17 l7 -2 v8 l-7 -1z" fill="var(--red)"/><rect x="17" y="10" width="10" height="3" fill="#fff"/><circle cx="22" cy="5" r="4" fill="var(--red)"/></svg></div>
    <h3>Merchant</h3>
    <p>Sed ut perspiciatis unde otsrs itvoluptatem accusan tium dolore mq ue laudpta te iu dololorlo</p>
  </div>
  <div class="step" style="left:384px">
    <div class="step-icon"><svg width="40" height="40" viewBox="0 0 40 40"><rect x="14" y="4" width="20" height="32" fill="none" stroke="var(--red)" stroke-width="3"/><path d="M20 6 L32 9 V33 L20 36 Z" fill="var(--red)"/><path d="M3 20 H16 M11 15 L16 20 L11 25" fill="none" stroke="var(--red)" stroke-width="3"/></svg></div>
    <h3>Sign in</h3>
    <p>Sed ut perspiciatis unde otsrs itvoluptatem accusan tium dolore mq ue laudpta te iu dololorlo</p>
  </div>
  <div class="step" style="left:618px">
    <div class="step-icon"><svg width="44" height="40" viewBox="0 0 44 40"><rect x="10" y="4" width="30" height="20" rx="2" transform="rotate(12 25 14)" fill="var(--red)" opacity=".55"/><rect x="4" y="12" width="32" height="22" rx="2" fill="var(--red)"/><rect x="4" y="17" width="32" height="4" fill="#fff"/><rect x="8" y="26" width="10" height="3" fill="#fff"/></svg></div>
    <h3>Card network</h3>
    <p>Sed ut perspiciatis unde otsrs itvoluptatem accusan tium dolore mq ue laudpta te iu dololorlo</p>
  </div>
  <div class="step" style="left:853px">
    <div class="step-icon"><svg width="36" height="40" viewBox="0 0 36 40"><path d="M9 18 V12 a9 9 0 0 1 18 0 V18" fill="none" stroke="var(--red)" stroke-width="4"/><rect x="4" y="18" width="28" height="20" rx="2" fill="var(--red)"/></svg></div>
    <h3>Easy checkout</h3>
    <p>Sed ut perspiciatis unde otsrs itvoluptatem accusan tium dolore mq ue laudpta te iu dololorlo</p>
  </div>
</section>

<h2 class="section-title dark" style="top:1771px">More reasons to use Zelnar</h2>

<article class="reason" style="left:160px">
  <div class="reason-photo" role="img" aria-label="Phone held over a contactless card reader" style="background:linear-gradient(135deg,#8a6a5d,#3b2f33 60%,#6b5a5f)"></div>
  <h3>Lorem ipsum dolor sit ame</h3>
  <p>Sed ut p loerspiciatis unde omnis iste natus error sit volup tatem accusantium dolore mq uloe laud antium, tota m rem aperiam, eaque ipsa quae ab.</p>
  <a class="btn read-more">Read more &rsaquo;</a>
</article>
<article class="reason" style="left:461px">
  <div class="reason-photo" role="img" aria-label="Hand holding a card beside a tablet" style="background:linear-gradient(135deg,#9bb3c9,#c9a890 55%,#6e6a78)"></div>
  <h3>Lorem ipsum dolor sit ame</h3>
  <p>Sed ut p loerspiciatis unde omnis iste natus error sit volup tatem accusantium dolore mq uloe laud antium, tota m rem aperiam, eaque ipsa quae ab.</p>
  <a class="btn read-more">Read more &rsaquo;</a>
</article>
<article class="reason" style="left:764px">
  <div class="reason-photo" role="img" aria-label="Customer entering a PIN on a card terminal" style="background:linear-gradient(135deg,#5b3a2c,#2a2526 50%,#c88a54)"></div>
  <h3>Lorem ipsum dolor sit ame</h3>
  <p>Sed ut p loerspiciatis unde omnis iste natus error sit volup tatem accusantium dolore mq uloe laud antium, tota m rem aperiam, eaque ipsa quae ab.</p>
  <a class="btn read-more">Read more &rsaquo;</a>
</article>

<section class="cta">
  <h2>Ready to get started? Get in touch,<br>or create an account</h2>
  <a class="btn">Create account &rsaquo;</a>
</section>

<footer>
  <div class="footer-col" style="left:160px">
    <h4>Products</h4>
    <ul><li>Payments</li><li>Subscriptions</li><li>Connect</li><li>Relay</li><li>Atlas</li></ul>
  </div>
  <div class="footer-col" style="left:345px">
    <h4>Developers</h4>
    <ul><li>Documentation</li><li>API reference</li><li>API status</li><li>Open source</li><li>Pricing</li><li>Customers</li></ul>
  </div>
  <div class="footer-col" style="left:535px">
    <h4>What we do</h4>
    <ul><li>Sed ut perspiciatis</li><li>Qnde omnis iste n</li><li>Wtus error sit voluptat</li><li>em accusantiu</li><li>Gdoloremque</li></ul>
  </div>
  <div class="footer-col" style="left:716px">
    <h4>Company</h4>
    <ul><li>Company info</li><li>News</li><li>Investors</li><li>Sed ut perspici</li><li>em accusantiu</li></ul>
  </div>
  <div class="footer-col" style="left:864px">
    <h4>Follow us</h4>
    <div class="socials"><span style="background:#3fa9e0"></span><span style="background:#2d5d9f"></span><span style="background:#1f74b0"></span><span style="background:#d9453a"></span></div>
    <p class="copyright">© 2016 All Copyrights are Reserved.<br><a>Privacy Policy</a><a>Sitemap</a></p>
  </div>
</footer>

</body>
</html>
```